Business Card design for law firm = Brightvale Australia

We are seeking a new design for our business cards.
We are keeping our logo, which is attached.
We need space for
Name
Title
Address is , which is
Level 7
214 Marlowe Street
Sydney NSW 2047
Phone :
Mobile :
Fax :
Email :
DX :
website www.brightvale-example.com.au

Industry/Entity Type

Law Firm / Banking and Finance

Contact Information for Business Card

We are seeking a new design for our business cards. We are keeping our logo. We need space for Name Title Address is Level 7 214 Marlowe Street Sydney NSW 2047 Phone Mobile Fax Email DX website www.brightvale-example.com.au

Colors
0054AA
0677BA
7BADD7
CADEEF
E8F1F8

Requirements
Must have
• see our website for general feel www.brightvale-example.com.au

```html
<!DOCTYPE html>
<html lang="en">
<head>
<meta charset="utf-8">
<title>Brightvale Business Card</title>
<link rel="stylesheet" href="https://fonts.googleapis.com/css2?family=EB+Garamond:ital,wght@0,400;1,400&display=swap">
<style>
  :root {
    --backdrop: #2b2b2c;
    --card-top: #1c1d1f;
    --card-bottom: #2a2b2e;
    --brand-navy: #2f4c9e;
    --brand-sky: #1591c6;
    --ink-light: #e6e6e6;
  }
  html, body {
    margin: 0;
    padding: 0;
    width: 1200px;
    height: 1138px;
    overflow: hidden;
    background: var(--backdrop);
  }
  .canvas {
    position: relative;
    width: 1200px;
    height: 1138px;
  }
  .card {
    position: absolute;
    width: 620px;
    height: 376px;
    border-radius: 16px;
    overflow: hidden;
    background: linear-gradient(160deg, var(--card-top) 35%, var(--card-bottom));
    box-shadow: 0 4px 10px rgba(0,0,0,0.45);
  }
  .card--front { left: 273px; top: 184px; }
  .card--back { left: 274px; top: 606px; }

  .brand {
    position: absolute;
    display: flex;
    align-items: center;
    white-space: nowrap;
  }
  .brand-dot {
    flex: none;
    background: var(--brand-sky);
  }
  .brand-name {
    margin: 0;
    font-family: "EB Garamond", serif;
    font-weight: 400;
    color: var(--ink-light);
    line-height: 1;
  }

  /* Front */
  .card--front .brand {
    left: 0; right: 0; top: 150px;
    justify-content: center;
  }
  .card--front .brand-dot { width: 16px; height: 16px; margin-right: 16px; }
  .card--front .brand-name { font-size: 52px; }
  .front-url {
    position: absolute;
    left: 0; right: 0; top: 336px;
    text-align: center;
    font-family: "EB Garamond", serif;
    font-size: 15px;
    letter-spacing: 7px;
    color: var(--ink-light);
    margin: 0;
  }
  .front-bar {
    position: absolute;
    left: 141px;
    width: 340px;
    bottom: 0;
    height: 8px;
    background: var(--brand-navy);
  }

  /* Back */
  .person-name {
    position: absolute;
    left: 32px; top: 40px;
    margin: 0;
    font-family: "EB Garamond", serif;
    font-weight: 400;
    font-size: 30px;
    color: var(--brand-navy);
    line-height: 1;
  }
  .name-rule { position: absolute; left: 20px; top: 72px; }
  .person-title {
    position: absolute;
    left: 32px; top: 82px;
    margin: 0;
    font-family: "EB Garamond", serif;
    font-style: italic;
    font-size: 17px;
    color: var(--ink-light);
  }
  .address {
    position: absolute;
    left: 33px; top: 208px;
    margin: 0;
    font-family: "EB Garamond", serif;
    font-style: normal;
    font-size: 16px;
    line-height: 21px;
    color: var(--ink-light);
  }
  .contact-list {
    position: absolute;
    left: 32px; top: 258px;
    margin: 0; padding: 0;
    list-style: none;
    font-family: "EB Garamond", serif;
    font-size: 16px;
    line-height: 20px;
    color: var(--ink-light);
  }
  .contact-list li { display: flex; align-items: center; }
  .contact-icon { width: 13px; height: 13px; margin-right: 18px; flex: none; }
  .card--back .brand { right: 32px; top: 300px; }
  .card--back .brand-dot { width: 11px; height: 11px; margin-right: 11px; }
  .card--back .brand-name { font-size: 34px; }
</style>
</head>
<body>
<main class="canvas">

  <section class="card card--front" aria-label="Card front">
    <div class="brand">
      <span class="brand-dot"></span>
      <h1 class="brand-name">Brightvale</h1>
    </div>
    <p class="front-url">www.brightvale-example.com.au</p>
    <div class="front-bar"></div>
  </section>

  <section class="card card--back" aria-label="Card back">
    <h2 class="person-name">Sam Whitlock</h2>
    <svg class="name-rule" width="194" height="6" viewBox="0 0 194 6" aria-hidden="true">
      <path d="M1 4 C60 1 140 1 193 2" stroke="#2f4c9e" stroke-width="2.4" fill="none" stroke-linecap="round"/>
    </svg>
    <p class="person-title">Managing Director</p>

    <address class="address">Level 7 214 Marlowe St<br>Sydney NSW 2047</address>

    <ul class="contact-list">
      <li>
        <svg class="contact-icon" viewBox="0 0 14 14" aria-hidden="true"><path fill="#1591c6" d="M1 5 C1 2 13 2 13 5 L10 5 L9.5 3.8 L4.5 3.8 L4 5 Z M3 6 L11 6 L12.5 12 L1.5 12 Z"/><circle cx="7" cy="9" r="1.6" fill="#1c1d1f"/></svg>
        02 9000 4812
      </li>
      <li>
        <svg class="contact-icon" viewBox="0 0 14 14" aria-hidden="true"><rect x="4" y="1" width="6" height="4" fill="#1591c6"/><rect x="1" y="5" width="12" height="5" rx="1" fill="#1591c6"/><rect x="4" y="9" width="6" height="4" fill="#1591c6" stroke="#1c1d1f" stroke-width="0.8"/></svg>
        02 9000 4813
      </li>
      <li>
        <svg class="contact-icon" viewBox="0 0 14 14" aria-hidden="true"><rect x="1" y="3" width="12" height="8" fill="#1591c6"/><path d="M1 3 L7 8 L13 3 M1 11 L5.5 7 M13 11 L8.5 7" stroke="#1c1d1f" stroke-width="0.9" fill="none"/></svg>
        sam.whitlock@brightvale-example.com.au
      </li>
      <li>
        <svg class="contact-icon" viewBox="0 0 14 14" aria-hidden="true"><circle cx="7" cy="7" r="5.8" fill="#1591c6"/><path d="M1.2 7 H12.8 M7 1.2 V12.8 M2.2 4.3 H11.8 M2.2 9.7 H11.8 M7 1.2 C4 4 4 10 7 12.8 M7 1.2 C10 4 10 10 7 12.8" stroke="#1c1d1f" stroke-width="0.7" fill="none"/></svg>
        www.brightvale-example.com.au
      </li>
    </ul>

    <div class="brand">
      <span class="brand-dot"></span>
      <p class="brand-name">Brightvale</p>
    </div>
  </section>

</main>
</body>
</html>
```